Car rental website design for a UAE car rental company

This project is about creating a new website design for a car rental company located in Dubai (United Arab Emirates), I opened the same project a few months ago but I didn't receive a lot of appealing entries so I closed it but this time I am marking the project as guaranteed to avoid such situation again, if you have already provided a design before then please re-submit again on this project so that it is considered while reviewing all the designs

A few important things:

1- We need a simple non-complex design
2- The final deliverable would be 2 screens (PSD, JPEG ... etc), the first screen is for the home page and the second screen is for an internal page
3- The home page must have a section that end users can use to rent a car online directly from the home page instead of going into some inner pages
4- The current website is very old and not very appealing so avoid creating a similar design (www.crestvane-autos.example)
5- The name is Crestvane but the company rents normal cars (no Limousin cars will be rented) so avoid adding any fancy cars in the images/graphics used in the design, just normal end users cars
6- The expected pages would be: home, About us, Our team, Strategy, Contact us and links to social media pages
7- The attachments include the company's logo and some screens from other car rental companies that provide online rentals/payments

If you have any questions please feel free to ask and please note that we will need the designs urgently

Thanks

Target Market(s)

Dubai - United Arab Emirates

Industry/Entity Type

It Company

Number of Pages Required

2 page

Font styles to use
Sans Serif

Requirements
Must have
• Check the project details
Nice to have
Should not have

```html
<!DOCTYPE html>
<html lang="en">
<head>
<meta charset="utf-8">
<title>Crestvane Rent A Car</title>
<link rel="stylesheet" href="https://fonts.googleapis.com/css2?family=Open+Sans:wght@400;600;700&family=Arimo:wght@400;700&display=swap">
<style>
:root{
  --crimson:#ae0a3d;
  --crimson-dark:#9c0f3c;
  --sage:#8a9a8c;
  --sage-dark:#7c8c7f;
  --gold:#e0b21f;
  --ink:#4a4a4a;
  --muted:#6d6d6d;
  --line:#dcdcdc;
  --panel:#f2f2f2;
  --white:#ffffff;
  --green:#6f9a1c;
}
*{box-sizing:border-box;margin:0;padding:0}
html,body{width:821px;height:1200px;overflow:hidden;background:var(--white)}
body{font-family:"Open Sans",Arial,sans-serif;color:var(--ink)}
.page{position:relative;width:821px;height:1200px;overflow:hidden;background:var(--white)}
.abs{position:absolute}

.top-bar{left:0;top:0;width:821px;height:4px;background:var(--sage)}
.header-rule{left:0;top:76px;width:821px;height:1px;background:var(--gold)}
.brand{left:103px;top:9px;width:142px;height:114px;background:var(--white);z-index:3;display:flex;align-items:center;justify-content:center;gap:6px}
.brand-mark{width:12px;height:12px;background:var(--crimson)}
.brand-name{font-family:"Open Sans",sans-serif;font-weight:700;font-size:19px;color:var(--sage-dark)}

.main-nav{top:34px;left:0;font-family:Arimo,Arial,sans-serif;font-weight:700;font-size:12px;color:var(--sage)}
.main-nav span{position:absolute;white-space:nowrap}
.main-nav .current{color:var(--crimson)}

.hero{left:0;top:77px;width:821px;height:310px;background:linear-gradient(100deg,#f0a43c 0%,#b8542a 18%,#3b2a3a 38%,#1a2238 60%,#2a3a66 85%,#324a80 100%)}
.hero-rule{left:0;top:386px;width:821px;height:2px;background:var(--gold)}
.hero-title{left:430px;top:186px;font-size:25px;font-weight:700;color:var(--white)}
.hero-text{left:431px;top:220px;width:285px;font-size:10px;line-height:13px;color:var(--white);text-align:justify}
.hero-link{left:638px;top:257px;font-size:10px;font-weight:600;color:var(--gold);display:flex;align-items:center;gap:6px}
.hero-cars{left:438px;top:324px;width:305px;height:105px;border-radius:40px 60px 10px 10px;background:linear-gradient(90deg,#2a2a2e 0%,#3a3a40 40%,#c8222a 60%,#d83a3a 100%)}
.slider-dot{width:9px;height:9px;border-radius:50%;left:751px}
.play-link{left:471px;top:432px;font-size:10px;font-weight:600;color:var(--green);display:flex;align-items:center;gap:6px}

.booking{left:103px;top:189px;width:301px;height:297px;background:var(--white);border:1px solid var(--line);border-radius:4px;z-index:2}
.tab{position:absolute;top:0;height:33px;font-size:11px;display:flex;align-items:center;justify-content:center}
.tab-book{left:0;width:142px;color:var(--crimson);background:var(--white)}
.tab-manage{left:142px;width:158px;background:var(--crimson);color:var(--white);border-radius:0 4px 0 0}
.field-label{position:absolute;font-size:8px;color:var(--muted);letter-spacing:.2px}
.input{position:absolute;border:1px solid var(--line);border-radius:4px;background:var(--white);font-size:9px;color:#9a9a9a;display:flex;align-items:center;padding-left:8px}
.checkbox{position:absolute;width:9px;height:9px;border:1px solid var(--line)}
.continue{position:absolute;left:171px;top:197px;width:106px;height:31px;background:var(--sage);color:var(--white);border-radius:3px;font-family:Arimo,Arial,sans-serif;font-size:13px;display:flex;align-items:center;justify-content:center}
.book-now{position:absolute;left:25px;top:239px;width:250px;height:40px;background:var(--crimson);color:var(--white);border-radius:3px;font-family:Arimo,Arial,sans-serif;text-align:center;line-height:1}
.book-now strong{display:block;font-weight:400;font-size:15px;margin-top:6px}
.book-now small{display:block;font-size:11px;margin-top:2px}

.divider{left:78px;top:495px;width:665px;border-top:1px dashed #cfcfcf}
.intro{left:91px;top:510px;width:191px}
.intro h2{font-size:11.5px;font-weight:600;line-height:14px;color:var(--ink);margin-bottom:14px}
.intro p{font-size:9px;line-height:12.5px;text-align:justify;color:var(--ink)}
.learn-more{left:91px;top:620px;font-size:10px;font-weight:600;display:flex;align-items:center;gap:7px}
.feature{width:196px}
.feature h3{font-size:11.5px;font-weight:600;color:var(--ink);display:flex;align-items:center;gap:8px;margin-bottom:10px;white-space:nowrap}
.feature p{font-size:9px;line-height:12.5px;text-align:justify;padding-left:5px}

.section-title{left:98px;top:708px;font-size:14.5px;font-weight:600;color:var(--ink)}
.car-card{top:741px;width:190px;height:331px;background:var(--panel)}
.car-photo{width:190px;height:122px}
.car-stripe{height:5px;background:var(--sage)}
.car-card h4{font-size:9.5px;font-weight:600;margin:6px 0 0 10px;color:var(--ink)}
.specs{margin:8px 0 0 10px;font-size:9px;color:var(--ink)}
.specs div{display:flex;height:20.5px}
.specs dt{width:103px}
.read-more{position:absolute;left:9px;bottom:10px;width:68px;height:23px;background:var(--crimson);color:var(--white);font-family:Arimo,Arial,sans-serif;font-size:11px;border-radius:2px;display:flex;align-items:center;justify-content:center}

.footer{left:0;top:1088px;width:821px;height:112px;background:var(--crimson-dark)}
.footer-nav{left:0;top:1104px;width:821px;text-align:center;font-family:Arimo,Arial,sans-serif;font-size:11px;color:var(--white)}
.social{left:0;top:1134px;width:821px;display:flex;justify-content:center;gap:10px}
.social span{width:26px;height:26px;border-radius:50%;background:#3a3a3a}
.copyright{left:0;top:1170px;width:821px;text-align:center;font-family:Arimo,Arial,sans-serif;font-size:8px;color:var(--white)}
.footer-rule{left:0;top:1193px;width:821px;height:1px;background:#d88aa0}
</style>
</head>
<body>
<div class="page">
  <div class="abs top-bar"></div>

  <div class="abs brand">
    <span class="brand-mark"></span>
    <span class="brand-name">Crestvane</span>
  </div>

  <nav class="abs main-nav">
    <span class="current" style="left:273px">Home</span>
    <span style="left:326px">Car Traveler</span>
    <span style="left:412px">Vehicles</span>
    <span style="left:479px">Locations</span>
    <span style="left:553px">My Bookings</span>
    <span style="left:643px">Help</span>
    <span style="left:690px">Contact us</span>
  </nav>
  <div class="abs header-rule"></div>

  <div class="abs hero" role="img" aria-label="Close-up of a dark blue car bonnet and wheel against a sunset sky"></div>
  <div class="abs hero-rule"></div>
  <h1 class="abs hero-title">Great car hire deals</h1>
  <p class="abs hero-text">Phasellus eget ultricies libero.Sed dolor turpis,malesuada vitae cursus a,auctor semper neque.</p>
  <div class="abs hero-link">
    <svg width="11" height="11" viewBox="0 0 12 12"><circle cx="6" cy="6" r="5.2" fill="none" stroke="#9a9a9a" stroke-width="1"/><path d="M4 6h4M6.3 4.2L8 6 6.3 7.8" fill="none" stroke="#9a9a9a" stroke-width="1"/></svg>
    Learn More
  </div>
  <div class="abs hero-cars" role="img" aria-label="A black hatchback and a red coupe side by side with a video play button"></div>
  <span class="abs slider-dot" style="top:334px;background:var(--white)"></span>
  <span class="abs slider-dot" style="top:348px;background:var(--crimson)"></span>
  <span class="abs slider-dot" style="top:362px;background:var(--crimson)"></span>
  <div class="abs play-link">
    <svg width="17" height="17" viewBox="0 0 18 18"><circle cx="9" cy="9" r="8.5" fill="var(--green)"/><path d="M7 5.5l5 3.5-5 3.5z" fill="#fff"/></svg>
    Play Now How it works
  </div>

  <form class="abs booking">
    <div class="tab tab-book">Book a Car</div>
    <div class="tab tab-manage">Manage Reservation</div>

    <span class="field-label" style="left:24px;top:50px">LOCATION</span>
    <div class="input" style="left:22px;top:63px;width:258px;height:32px">Enter City or Zip code</div>
    <span class="checkbox" style="left:26px;top:104px"></span>
    <span class="field-label" style="left:40px;top:104px">Return at different location</span>

    <span class="field-label" style="left:24px;top:131px">PICK-UP DATE</span>
    <div class="input" style="left:23px;top:143px;width:79px;height:31px">
      <svg width="10" height="10" viewBox="0 0 10 10"><rect x=".5" y="1.5" width="9" height="8" fill="none" stroke="#999"/><path d="M.5 3.5h9M3 0v2M7 0v2" stroke="#999"/></svg>
    </div>
    <div class="input" style="left:106px;top:143px;width:37px;height:31px"></div>
    <span class="field-label" style="left:165px;top:131px">DROP-OFF DATE</span>
    <div class="input" style="left:162px;top:143px;width:79px;height:31px">
      <svg width="10" height="10" viewBox="0 0 10 10"><rect x=".5" y="1.5" width="9" height="8" fill="none" stroke="#999"/><path d="M.5 3.5h9M3 0v2M7 0v2" stroke="#999"/></svg>
    </div>
    <div class="input" style="left:244px;top:143px;width:37px;height:31px"></div>

    <span class="field-label" style="left:24px;top:183px">CAR TYPE</span>
    <div class="input" style="left:23px;top:197px;width:80px;height:30px;justify-content:space-between;padding-right:8px">Standard
      <svg width="7" height="4" viewBox="0 0 7 4"><path d="M0 0h7L3.5 4z" fill="#999"/></svg>
    </div>
    <div class="continue">Continue</div>
    <div class="book-now"><strong>Book Now Car for Rental</strong><small>Try its to first Booking</small></div>
  </form>

  <div class="abs divider"></div>

  <section class="abs intro">
    <h2>We are leading car rental agency with 300,000 Happy Customers.</h2>
    <p>Morbi orci ante,consectetur id vestibulum quis,suscipit eu eros.Duis non egestas dolor.Duis non volutpat leo.Aliquam nisi eros,accumsan non gravida vitae,ultrices eu eros.Phasellus sagittis mattis tristique.</p>
  </section>
  <div class="abs learn-more">
    <svg width="11" height="11" viewBox="0 0 12 12"><circle cx="6" cy="6" r="5.2" fill="none" stroke="#9a9a9a"/><path d="M4 6h4M6.3 4.2L8 6 6.3 7.8" fill="none" stroke="#9a9a9a"/></svg>
    Learn More
  </div>

  <article class="abs feature" style="left:305px;top:509px">
    <h3><svg width="12" height="12" viewBox="0 0 12 12"><path d="M1 1h5l5 5-5 5-5-5z" fill="#555"/><circle cx="3.5" cy="3.5" r="1" fill="#fff"/></svg>Special low rates on car booking</h3>
    <p>Nunc ut nibh enim,id dapibus quam.Mauris id est at diam rutrum ultricies.Vivamus et dolor velit.Nam congue blandit nulla sed tincidunt.</p>
  </article>
  <article class="abs feature" style="left:526px;top:509px">
    <h3><svg width="12" height="12" viewBox="0 0 12 12"><rect x="1" y="2" width="9" height="9" fill="none" stroke="#555" stroke-width="1.3"/><path d="M5 7l6-6" stroke="#555" stroke-width="1.6"/></svg>Manage your booking online</h3>
    <p>Nunc ut nibh enim,id dapibus quam.Mauris id est at diam rutrum ultricies.Vivamus et dolor velit.Nam congue blandit nulla sed tincidunt.</p>
  </article>
  <article class="abs feature" style="left:305px;top:606px">
    <h3><svg width="12" height="12" viewBox="0 0 12 12"><circle cx="6" cy="6" r="4.6" fill="none" stroke="#555" stroke-width="1.6"/><circle cx="6" cy="6" r="1.6" fill="#555"/></svg>Special low rates on car booking</h3>
    <p>Nunc ut nibh enim,id dapibus quam.Mauris id est at diam rutrum ultricies.Vivamus et dolor velit.Nam congue blandit nulla sed tincidunt.</p>
  </article>
  <article class="abs feature" style="left:526px;top:606px">
    <h3><svg width="12" height="12" viewBox="0 0 12 12"><circle cx="6" cy="6" r="5" fill="none" stroke="#555" stroke-width="1.3"/><path d="M6 3v3l2 2" fill="none" stroke="#555" stroke-width="1.3"/></svg>Manage your booking online</h3>
    <p>Nunc ut nibh enim,id dapibus quam.Mauris id est at diam rutrum ultricies.Vivamus et dolor velit.Nam congue blandit nulla sed tincidunt.</p>
  </article>

  <h2 class="abs section-title">3 FEATURED CARS</h2>

  <article class="abs car-card" style="left:98px">
    <div class="car-photo" role="img" aria-label="Dark blue saloon car parked by a stone building" style="background:linear-gradient(180deg,#b9b6ae 0%,#8f8c84 45%,#2e2f5a 65%,#a9a49a 100%)"></div>
    <div class="car-stripe"></div>
    <h4>ABOUT THE CAR</h4>
    <dl class="specs">
      <div><dt>Car type</dt><dd>Car</dd></div>
      <div><dt>Maks. pers</dt><dd>2</dd></div>
      <div><dt>Ant. Doors</dt><dd>4</dd></div>
      <div><dt>Min. driver age</dt><dd>21</dd></div>
      <div><dt>Gearbox</dt><dd>Manual</dd></div>
      <div><dt>Air Conditioning?</dt><dd>yes</dd></div>
      <div><dt>Unlimited km?</dt><dd>in the</dd></div>
    </dl>
    <span class="read-more">Read more</span>
  </article>

  <article class="abs car-card" style="left:314px">
    <div class="car-photo" role="img" aria-label="Red sports coupe on a white background" style="background:radial-gradient(ellipse at 55% 45%,#d8202c 0%,#b51822 30%,#f4f4f4 62%,#ffffff 100%)"></div>
    <div class="car-stripe"></div>
    <h4>ABOUT THE CAR</h4>
    <dl class="specs">
      <div><dt>Car type</dt><dd>Car</dd></div>
      <div><dt>Maks. pers</dt><dd>2</dd></div>
      <div><dt>Ant. Doors</dt><dd>4</dd></div>
      <div><dt>Min. driver age</dt><dd>21</dd></div>
      <div><dt>Gearbox</dt><dd>Manual</dd></div>
      <div><dt>Air Conditioning?</dt><dd>yes</dd></div>
      <div><dt>Unlimited km?</dt><dd>in the</dd></div>
    </dl>
    <span class="read-more">Read more</span>
  </article>

  <article class="abs car-card" style="left:531px">
    <div class="car-photo" role="img" aria-label="Red estate car driving on a coastal road" style="background:linear-gradient(180deg,#c9c2b3 0%,#9a8f7c 35%,#c9242c 60%,#6b6a66 100%)"></div>
    <div class="car-stripe"></div>
    <h4>ABOUT THE CAR</h4>
    <dl class="specs">
      <div><dt>Car type</dt><dd>Car</dd></div>
      <div><dt>Maks. pers</dt><dd>2</dd></div>
      <div><dt>Ant. Doors</dt><dd>4</dd></div>
      <div><dt>Min. driver age</dt><dd>21</dd></div>
      <div><dt>Gearbox</dt><dd>Manual</dd></div>
      <div><dt>Air Conditioning?</dt><dd>yes</dd></div>
      <div><dt>Unlimited km?</dt><dd>in the</dd></div>
    </dl>
    <span class="read-more">Read more</span>
  </article>

  <footer class="abs footer"></footer>
  <nav class="abs footer-nav">Home &nbsp;| &nbsp;Car Traveler &nbsp;| Vehicles &nbsp;| Locations &nbsp;| My Bookings &nbsp;| Help &nbsp;| Contact us</nav>
  <div class="abs social" aria-label="Social media links">
    <span></span><span></span><span></span><span></span><span></span>
  </div>
  <p class="abs copyright">Copyright © crestvane-autos.example,2015, All Right Reserved.</p>
  <div class="abs footer-rule"></div>
</div>
</body>
</html>
```